real esate business card with company logo and name

we need a business card design for a real esate company

The company name is Walsh & Brand Pty Ltd, and we have our logo designed and will upload. We want classic or moden feel. Black or white background. looks more textured. Should include folowinginformations
Owen Walsh and Lucy Brand
Sales Agents & Onsite Manager
p: 07 5948 2063
F: 07 5948 2174
M:0431 857 219
3/42 Marlow Crescent, FERNLEA QLD 4213

We want this business card looks professonal. Thank you in advance.

Industry/Entity Type

Real Estate Agent

Contact Information for Business Card

Owen Walsh and Lucy Brand
Onsite Manager & Sales Agents
p: 07 5948 2063
M:0431 857 219

Font styles to use
Serif

Colors
000000
fbfbfb
333333
959595

Requirements
Must have
• company logo and name, black or white back ground

```html
<!DOCTYPE html>
<html lang="en">
<head>
<meta charset="utf-8">
<title>Walsh &amp; Brand Pty Ltd – Business Card</title>
<link rel="stylesheet" href="https://fonts.googleapis.com/css2?family=Open+Sans:wght@400;600&display=swap">
<style>
  :root {
    --page: #e4e4e2;
    --ink-dark: #333333;
    --ink-black: #1f1f1f;
    --paper: #fbfbfb;
    --mid-grey: #959595;
    --band-grey: #b9b9b9;
    --text-light: #f4f4f4;
    --phone-tint: #e8a994;
    --address-tint: #d8bc62;
  }
  html, body {
    margin: 0;
    width: 1200px;
    height: 952px;
    overflow: hidden;
    background: var(--page);
    font-family: "Open Sans", Arial, sans-serif;
  }
  .card {
    position: absolute;
    left: 120px;
    top: 182px;
    width: 960px;
    height: 587px;
    border-radius: 10px;
    overflow: hidden;
    background: var(--paper);
    box-shadow: 0 14px 40px rgba(0,0,0,0.18);
  }
  .card-shapes { position: absolute; inset: 0; }
  .names {
    position: absolute;
    left: 44px;
    top: 50px;
    margin: 0;
    font-weight: 400;
    font-size: 36px;
    line-height: 1.2;
    white-space: nowrap;
    color: var(--text-light);
  }
  .role {
    position: absolute;
    left: 46px;
    top: 104px;
    margin: 0;
    font-size: 22px;
    white-space: nowrap;
    color: #d6d6d6;
  }
  .contact {
    position: absolute;
    left: 150px;
    top: 222px;
    width: 380px;
    text-align: center;
    color: var(--text-light);
    font-size: 23px;
    line-height: 1.2;
  }
  .contact-item { margin: 0 0 14px; }
  .contact-icon {
    display: block;
    margin: 0 auto 8px;
    width: 22px;
    height: 22px;
  }
  .phone-number { color: var(--phone-tint); }
  .address { color: var(--address-tint); line-height: 1.55; }
  .brand {
    position: absolute;
    left: 625px;
    top: 150px;
    width: 320px;
    text-align: center;
  }
  .brand-square {
    width: 150px;
    height: 150px;
    margin: 0 auto 36px;
    background: var(--mid-grey);
  }
  .brand-name {
    margin: 0;
    font-weight: 600;
    font-size: 21px;
    letter-spacing: 1.5px;
    white-space: nowrap;
    text-transform: uppercase;
    color: #5a5a5a;
  }
</style>
</head>
<body>
  <div class="card">
    <svg class="card-shapes" width="960" height="587" viewBox="0 0 960 587">
      <path d="M0 0 H620 C550 200 580 460 690 587 H0 Z" fill="var(--band-grey)"/>
      <path d="M0 0 H600 C530 200 560 460 668 587 H0 Z" fill="var(--ink-dark)"/>
    </svg>

    <h1 class="names">Owen Walsh and Lucy Brand</h1>
    <p class="role">Onsite Manager &amp; Sales Agents</p>

    <div class="contact">
      <p class="contact-item phone-number">
        <svg class="contact-icon" viewBox="0 0 22 22"><rect width="22" height="22" rx="2" fill="#eee"/><path d="M6 4 l3 0 1 4 -2 1.5 c1 2 2.5 3.5 4.5 4.5 l1.5-2 4 1 0 3 c-7 1-13-5-12-12z" fill="var(--ink-black)"/></svg>
        07 5948 2063
      </p>
      <p class="contact-item">
        <svg class="contact-icon" viewBox="0 0 22 22"><rect width="22" height="22" rx="2" fill="#eee"/><rect x="7" y="3" width="8" height="16" rx="1.5" fill="var(--ink-black)"/><rect x="8.5" y="5" width="5" height="7" fill="#eee"/></svg>
        0431 857 219
      </p>
      <p class="contact-item address">
        <svg class="contact-icon" viewBox="0 0 22 22"><rect width="22" height="22" rx="2" fill="#eee"/><path d="M11 4 L18 11 H16 V18 H13 V14 H9 V18 H6 V11 H4 Z" fill="var(--ink-black)"/></svg>
        3/42 Marlow Crescent,<br>FERNLEA QLD 4213
      </p>
    </div>

    <div class="brand">
      <div class="brand-square"></div>
      <p class="brand-name">Walsh &amp; Brand Pty Ltd</p>
    </div>
  </div>
</body>
</html>
```